Black Car Limousine transportation business in Naples Florida

Always stand for my reliability and RVD stands for Love, K and M are the first initials of my children's names. It should show professionalism and a dedication to customer service. We keep our clients identities private. Show our professionalism. We are Black car Black tie company. We service transportation on a reserve basis to and from residents, airports, casinos, hotels,

Target Market(s)

It is a Private car service. High end clients. Businesses, Celebrity and athletes. Service to airports, hotels, special events.

Industry/Entity Type

Business

Contact Information for Business Card

A pearl metallic or Luster card. Standard business card size. Would like the name, Company email, show we take credit cards and phone number. Currently I don't have a website but will like to add later.

Logo Text

STEADFAST RVD TRANSPORTATION

Font styles to use
Serif

Colors
eaeaea
000000

Requirements
Must have
• Must have Company email, show we take credit cards and phone number. Currently I don't have a website but will like to add later.
Nice to have
• Would like to stay with a black and white theme. Open to some color trim.
Should not have
• Open to suggestions

```html
<!DOCTYPE html>
<html lang="en">
<head>
<meta charset="utf-8">
<title>Steadfast RVD Transportation – Business Card</title>
<link rel="stylesheet" href="https://fonts.googleapis.com/css2?family=Cormorant+Garamond:wght@500;600;700&display=swap">
<style>
  :root {
    --backdrop: #3a3330;
    --card: #000000;
    --ink-light: #eaeaea;
    --ink-muted: #bdbdbd;
  }
  * { margin: 0; padding: 0; box-sizing: border-box; }
  html, body {
    width: 1200px;
    height: 900px;
    overflow: hidden;
    background: var(--backdrop);
    font-family: "Cormorant Garamond", Georgia, serif;
  }
  .canvas {
    position: relative;
    width: 1200px;
    height: 900px;
  }
  .card {
    position: absolute;
    top: 300px;
    width: 525px;
    height: 300px;
    background: var(--card);
    border-radius: 3px;
    box-shadow: 0 10px 30px rgba(0,0,0,0.45);
  }
  .card--front { left: 50px; }
  .card--back { left: 625px; }

  .wordmark {
    position: absolute;
    color: var(--ink-light);
    font-weight: 600;
    text-transform: uppercase;
    line-height: 1;
    text-align: center;
  }
  .wordmark__line { display: block; }
  .wordmark__line--small { font-size: 20px; letter-spacing: 4px; }
  .wordmark__line--large { font-size: 62px; letter-spacing: 6px; margin: 4px 0 2px; }

  .card--front .wordmark { top: 44px; right: 44px; }
  .card--front .wordmark__line--small { font-size: 16px; letter-spacing: 3px; }
  .card--front .wordmark__line--large { font-size: 48px; letter-spacing: 5px; }

  .card--back .wordmark {
    top: 50%;
    left: 50%;
    transform: translate(-50%, -50%);
    white-space: nowrap;
  }

  .contact {
    position: absolute;
    left: 36px;
    bottom: 30px;
  }
  .contact__name {
    color: var(--ink-light);
    font-size: 26px;
    font-weight: 700;
    margin-bottom: 10px;
  }
  .contact__row {
    display: flex;
    align-items: center;
    gap: 10px;
    color: var(--ink-muted);
    font-size: 16px;
    font-weight: 500;
    line-height: 22px;
  }
  .contact__icon { width: 13px; height: 13px; flex: none; }
</style>
</head>
<body>
<main class="canvas">
  <section class="card card--front" aria-label="Business card front">
    <div class="wordmark">
      <span class="wordmark__line wordmark__line--small">Steadfast</span>
      <span class="wordmark__line wordmark__line--large">RVD</span>
      <span class="wordmark__line wordmark__line--small">Transportation</span>
    </div>
    <div class="contact">
      <p class="contact__name">Marco Delvane</p>
      <p class="contact__row">
        <svg class="contact__icon" viewBox="0 0 24 24" aria-hidden="true">
          <path fill="#eaeaea" d="M6.6 10.8a15.1 15.1 0 0 0 6.6 6.6l2.2-2.2a1 1 0 0 1 1-.25 11.4 11.4 0 0 0 3.6.57 1 1 0 0 1 1 1V20a1 1 0 0 1-1 1A17 17 0 0 1 3 4a1 1 0 0 1 1-1h3.5a1 1 0 0 1 1 1c0 1.25.2 2.45.57 3.57a1 1 0 0 1-.25 1z"/>
        </svg>
        877-555-0142
      </p>
      <p class="contact__row">
        <svg class="contact__icon" viewBox="0 0 24 24" aria-hidden="true">
          <rect x="2" y="5" width="20" height="14" rx="1" fill="#eaeaea"/>
          <path d="M2 6l10 7 10-7" fill="none" stroke="#000" stroke-width="2"/>
        </svg>
        steadfastrvdtransportation@mail.com
      </p>
      <p class="contact__row">
        <svg class="contact__icon" viewBox="0 0 24 24" aria-hidden="true">
          <rect x="2" y="5" width="20" height="14" rx="2" fill="none" stroke="#eaeaea" stroke-width="2"/>
          <rect x="2" y="9" width="20" height="3" fill="#eaeaea"/>
        </svg>
        All major credit cards accepted
      </p>
    </div>
  </section>

  <section class="card card--back" aria-label="Business card back">
    <div class="wordmark">
      <span class="wordmark__line wordmark__line--small">Steadfast</span>
      <span class="wordmark__line wordmark__line--large">RVD</span>
      <span class="wordmark__line wordmark__line--small">Transportation</span>
    </div>
  </section>
</main>
</body>
</html>
```